Business Card Design for BrightvaleMedia.com

--I need a business card design for my company BrightvaleMedia.com

I have attached my logo...I want the brightvale media logo on the front of the business card, and then I want The Quillstone Chief on the back of it with my information.

I would like to see a light colored background as well as a dark colored background

FRONT:
BRIGHTVALE MEDIA LOGO
248 N. Larkmoor
3rd Floor
San Diego CA 92173
www.BrightvaleMedia.com

Advanced Website & App Development
Websites, Apps, Online Voucher Systems

Leading Edge Marketing Services
SMS, VB, SMM, SEM,

BACK:
QUILLSTONE CHIEF LOGO
Dorian Pelletta
The Quillstone Chief
Call Or Text: 619-555-0148
Dorian@QuillstoneChief.example
www.QuillstoneChief.example

Target Market(s)

small business owners

Industry/Entity Type

Business Consultant

Contact Information for Business Card

FRONT:
BRIGHTVALE MEDIA LOGO
248 N. Larkmoor
3rd Floor
San Diego CA 92173
www.BrightvaleMedia.com

SMS, VB, SMM, SEM,

BACK:
QUILLSTONE CHIEF LOGO
Dorian Pelletta
The Quillstone Chief
Dorian@QuillstoneChief.example
www.QuillstoneChief.example

Requirements
Must have
• add this quote on it somewhere, anywhere,preferrably on back
• "The Fastest Way To Success Is To Take Action”
• — Dorian Pelletta, Quillstone Chief
Nice to have
• open
Should not have
• red

```html
<!DOCTYPE html>
<html lang="en">
<head>
<meta charset="utf-8">
<title>Brightvale Media – Business Card</title>
<link href="https://fonts.googleapis.com/css2?family=Open+Sans:wght@400;600;700&display=swap" rel="stylesheet">
<style>
  :root {
    --backdrop: #3b3b3b;
    --brand-blue: #0272ab;
    --paper: #ffffff;
    --ink-light: #ffffff;
  }
  * { margin: 0; padding: 0; box-sizing: border-box; }
  html, body {
    width: 1105px; height: 1200px; overflow: hidden;
    background: var(--backdrop);
    font-family: "Open Sans", sans-serif;
  }
  .canvas { position: relative; width: 1105px; height: 1200px; }

  .card {
    position: absolute; left: 196px; width: 720px; height: 411px; overflow: hidden;
  }
  .card--front { top: 146px; background: var(--brand-blue); color: var(--ink-light); }
  .card--back { top: 602px; background: var(--paper); }

  .brand-name {
    position: absolute; left: 60px; top: 56px;
    font-weight: 600; font-size: 40px; letter-spacing: 2px; line-height: 1.1;
    color: var(--ink-light);
  }
  .front-info {
    position: absolute; left: 60px; top: 140px;
    font-size: 19px; line-height: 26px;
  }
  .front-info .web { font-weight: 700; }
  .front-info .group { margin-bottom: 12px; }

  .chief-name {
    position: absolute; right: 55px; top: 92px;
    font-weight: 600; font-size: 34px; letter-spacing: 1.5px;
    color: var(--brand-blue);
  }
  .info-band {
    position: absolute; left: 0; top: 240px; width: 720px; height: 133px;
    background: var(--brand-blue); color: var(--ink-light);
  }
  .person { position: absolute; left: 54px; top: 38px; }
  .person-name { font-size: 25px; font-weight: 700; line-height: 32px; }
  .person-title { font-size: 19px; line-height: 26px; }
  .contact-list {
    position: absolute; left: 384px; top: 26px; list-style: none;
    font-size: 18px; line-height: 28px; white-space: nowrap;
  }
  .contact-list li { display: flex; align-items: center; gap: 10px; }
  .contact-list svg { width: 18px; height: 18px; fill: var(--ink-light); flex: none; }

  .quote {
    position: absolute; left: 0; top: 373px; width: 720px; height: 38px;
    text-align: center; font-size: 14px; line-height: 38px;
    color: var(--brand-blue); white-space: nowrap;
  }
</style>
</head>
<body>
<main class="canvas">
  <section class="card card--front" aria-label="Card front">
    <div class="brand-name">BRIGHTVALE MEDIA</div>
    <div class="front-info">
      <div class="group">
        <p>248 N. Larkmoor, 3rd Floor</p>
        <p>San Diego CA 92173</p>
        <p class="web">www.BrightvaleMedia.com</p>
      </div>
      <div class="group">
        <p>Advanced Website &amp; App Development</p>
        <p>Websites • Apps • Online Voucher Systems</p>
      </div>
      <div class="group">
        <p>Leading Edge Marketing Services</p>
        <p>SMS • VB • SMM • SEM</p>
      </div>
    </div>
  </section>

  <section class="card card--back" aria-label="Card back">
    <div class="chief-name">QUILLSTONE CHIEF</div>
    <div class="info-band">
      <div class="person">
        <p class="person-name">DORIAN PELLETTA</p>
        <p class="person-title">The Quillstone Chief</p>
      </div>
      <ul class="contact-list">
        <li>
          <svg viewBox="0 0 24 24" aria-hidden="true"><path d="M6.6 10.8a15.1 15.1 0 0 0 6.6 6.6l2.2-2.2a1 1 0 0 1 1-.25 11.4 11.4 0 0 0 3.6.57 1 1 0 0 1 1 1V20a1 1 0 0 1-1 1A17 17 0 0 1 3 4a1 1 0 0 1 1-1h3.5a1 1 0 0 1 1 1c0 1.25.2 2.45.57 3.6a1 1 0 0 1-.25 1z"/></svg>
          619-555-0148
        </li>
        <li>
          <svg viewBox="0 0 24 24" aria-hidden="true"><path d="M2 6.5V19h20V6.5l-10 7.5z"/><path d="M2.5 5h19L12 12.2z"/></svg>
          Dorian@QuillstoneChief.example
        </li>
        <li>
          <svg viewBox="0 0 24 24" aria-hidden="true"><circle cx="12" cy="12" r="9.5"/><path d="M7 7l4 1 1 3-3 2 1 4-3-2-1-4z M14 6l3 1 2 4-3 1-2-2z" fill="#0272ab"/></svg>
          www.QuillstoneChief.example
        </li>
      </ul>
    </div>
    <p class="quote">“The Fastest Way To Success Is To Take Action” — Dorian Pelletta, Quillstone Chief</p>
  </section>
</main>
</body>
</html>
```